New Business Card Design for Manufacturing

We are an engineering/manufacturing company that offers Advanced machining/assembly/engineering services, as well as innovative products for the heavy duty engine cooling markets.

We are looking to get a new business card designed that is clean and modern looking, but still fits the wide range of technical/skilled work we do.

- We hope to use this design as the base for other design work in new Presentations, web, and print work.

Industry/Entity Type

Engineering

Contact Information for Business Card

Our preferred color of blue is (RGB) 22/71/159 but can vary slightly from that color. Our content will be our Logo and full company name (Vantrell Forge Works, Inc.), company address, name, job title, phone number with extension, cell number, fax number, website, and email address on the cards.
We'd like the full company name next to the logo, but we are open to other interpretations of that layout.
Preferably, we would like the back side to be clean with just our logo, and the front to contain all of the contact information.

Colors
2f74b4
0355a3
85abd2

Requirements
Must have
• - Logo, company name, needed content - We are open to interpretation beyond that.
• - Standard size business card.
• - Horizontal orientation.
• - Enough space for lengthy names / job titles (for example, a job title could read "Directory of Human Resources" or "V.P. of Governmental Affairs"). We need this to look clean, whether the title be short (CEO) or long (as described above).

```html
<!DOCTYPE html>
<html lang="en">
<head>
<meta charset="utf-8">
<title>Vantrell Forge Works – Business Card</title>
<link rel="stylesheet" href="https://fonts.googleapis.com/css2?family=Open+Sans:wght@400;600;800&display=swap">
<style>
  :root {
    --brand-blue: #16479f;
    --brand-blue-deep: #0355a3;
    --emboss-blue: #6a97dc;
    --ink-grey: #6d6e71;
    --line-grey: #a7a9ac;
    --card-white: #ffffff;
    --stage: #e9ebef;
  }
  * { box-sizing: border-box; margin: 0; padding: 0; }
  html, body { width: 1200px; height: 862px; overflow: hidden; }
  body {
    background: var(--stage);
    font-family: "Open Sans", Arial, sans-serif;
    position: relative;
  }
  .card {
    position: absolute;
    width: 620px;
    height: 354px;
    border-radius: 22px;
    overflow: hidden;
    box-shadow: 0 6px 18px rgba(0,0,0,0.12);
  }

  /* Back side */
  .card--back {
    left: 60px; top: 60px;
    background: var(--brand-blue);
  }
  .card--back .wordmark {
    position: absolute;
    left: 0; right: 0; top: 128px;
    text-align: center;
    font-weight: 800;
    font-size: 40px;
    letter-spacing: 0.5px;
    color: var(--emboss-blue);
  }
  .card--back .web {
    position: absolute;
    left: 0; right: 0; top: 232px;
    text-align: center;
    font-size: 12px;
    color: var(--emboss-blue);
  }

  /* Front side */
  .card--front {
    left: 520px; top: 448px;
    background: var(--card-white);
  }
  .card--front .wave {
    position: absolute; left: 0; top: 0;
    width: 620px; height: 354px;
  }
  .card--front .wordmark {
    position: absolute;
    left: 40px; top: 150px;
    width: 270px;
    font-weight: 800;
    font-size: 30px;
    line-height: 1.1;
    color: var(--brand-blue);
  }
  .card--front .divider {
    position: absolute;
    left: 340px; top: 36px;
    width: 1px; height: 168px;
    background: var(--line-grey);
  }
  .contact {
    position: absolute;
    left: 358px; top: 36px;
    color: var(--ink-grey);
    font-size: 11px;
    line-height: 1.55;
  }
  .contact .name {
    font-weight: 800;
    font-size: 17px;
    color: var(--brand-blue);
    line-height: 1.2;
  }
  .contact .title { margin-bottom: 6px; }
  .contact .address { margin-bottom: 6px; }
  .contact ul { list-style: none; }
  .contact li { display: flex; align-items: center; gap: 8px; }
  .contact li svg { width: 10px; height: 10px; fill: var(--brand-blue); flex: none; }
</style>
</head>
<body>

<section class="card card--back" aria-label="Card back">
  <div class="wordmark">Vantrell Forge Works</div>
  <div class="web">www.vantrellforge.com</div>
</section>

<section class="card card--front" aria-label="Card front">
  <svg class="wave" viewBox="0 0 620 354" aria-hidden="true">
    <path d="M0 308 C 200 306, 400 282, 620 222 L620 232 C 400 294, 200 318, 0 320 Z" fill="var(--line-grey)"/>
    <path d="M0 328 C 210 326, 410 300, 620 242 L620 354 L0 354 Z" fill="var(--brand-blue)"/>
  </svg>

  <div class="wordmark">Vantrell Forge Works</div>
  <div class="divider"></div>

  <div class="contact">
    <div class="name">Marlon Keats</div>
    <div class="title">President</div>
    <div class="address">Street Name Avenue, Suite 100<br>State, Zip Code Country</div>
    <ul>
      <li><svg viewBox="0 0 10 10"><path d="M2 0 L4 2.5 L3 3.6 C3.6 5 5 6.4 6.4 7 L7.5 6 L10 8 L8.6 9.8 C4.5 9.5 0.5 5.5 0.2 1.4 Z"/></svg>+000.000.00.00</li>
      <li><svg viewBox="0 0 10 10"><path d="M2.5 0 H7.5 V10 H2.5 Z M3.5 1 V8 H6.5 V1 Z"/></svg>+000.000.00.00</li>
      <li><svg viewBox="0 0 10 10"><path d="M2 0 H7 V3 H2 Z M0 3.5 H10 V8 H8 V10 H2 V8 H0 Z"/></svg>+000.000.00.00</li>
      <li><svg viewBox="0 0 10 10"><path d="M0 2 H10 V8 H0 Z M0.8 2.6 L5 5.6 L9.2 2.6"/></svg>info@vantrellforge.com</li>
      <li><svg viewBox="0 0 10 10"><circle cx="5" cy="5" r="5"/></svg>www.vantrellforge.com</li>
    </ul>
  </div>
</section>

</body>
</html>
```